Construction proffessionals servicing the inner suburbs of Melbournes NorthWest specialising in aler

I would like a web site that is sharp, contemporary and simple to navigate, ie.not too many pages. i would like a home page with some info about us, who we are what our history is and my passion for building and construction based on impeccable customer focus. i would like a projects page and somewhere for clients to add testimonials. i would like a project calculator as well so prospective clients can work out a rough budget prior to contacting. i would like the colours to be in line with my logo which i have uploaded. i have many photos which can be used and can be shared via drop box when required. I would like it to be personal to capture our transparent process. i would like to add our company process as well. be brave and take risks.

Target Market(s)

People renovating and extending their homes, people needing inspections on new homes and pre-purchase inspections

Industry/Entity Type

Construction

Number of Pages Required

5+ page

Requirements
Must have
• Professional, easy to navigate, provide viewers with a happy experience, look great, contacts, project calculator, link through to my training company www.qdmn.learnhub.example also check rowenhq on instagram for pics
Nice to have
• Links to instagram, fonts to match email signature

```html
<!DOCTYPE html>
<html lang="en">
<head>
<meta charset="utf-8">
<title>Rowen Group Pty Ltd</title>
<link href="https://fonts.googleapis.com/css2?family=Open+Sans:ital,wght@0,400;0,600;0,700;1,400&display=swap" rel="stylesheet">
<style>
:root{
  --orange:#f08a1c;
  --orange-dark:#d9760f;
  --ink:#3a3a3a;
  --muted:#7d7d7d;
  --band:#ececec;
  --page:#e9e9e9;
  --footer:#4b3b2f;
  --footer-text:#cdbfb2;
  --bar:#3a2d24;
  --white:#ffffff;
}
*{margin:0;padding:0;box-sizing:border-box}
html,body{width:839px;height:1200px;overflow:hidden}
body{background:var(--page);font-family:"Open Sans",Arial,sans-serif;color:var(--ink)}
.page{width:660px;height:1200px;margin:0 auto;background:var(--white);display:flex;flex-direction:column}

.site-header{height:50px;flex:none;display:flex;align-items:center;justify-content:space-between;padding:0 36px}
.brand{display:flex;align-items:center;gap:6px;font-weight:700;font-size:20px;color:var(--orange);letter-spacing:1px}
.brand-square{width:14px;height:14px;background:var(--orange)}
.call{text-align:right}
.call small{display:block;font-size:6.5px;font-weight:700;color:var(--orange);letter-spacing:.5px}
.call .phone{display:flex;align-items:center;gap:4px;font-size:14px;font-weight:600;color:var(--ink)}

.main-nav{height:18px;flex:none;background:var(--orange);display:flex;justify-content:center}
.main-nav a{color:var(--white);font-size:6.5px;font-weight:600;text-decoration:none;line-height:18px;padding:0 13px;border-right:1px solid var(--orange-dark)}
.main-nav a:last-child{border-right:0}
.main-nav a.active{background:var(--orange-dark)}

.hero{position:relative;height:350px;flex:none;background:
  linear-gradient(180deg,#b9c8d6 0%,#a9b5bf 22%,#8d8276 40%,#7a6c60 70%,#978a7d 100%)}
.hero-caption{position:absolute;left:36px;top:128px;color:var(--white);width:260px}
.hero-caption .kicker{font-size:11px;font-weight:600}
.hero-caption h1{font-size:24px;font-weight:700;line-height:1.15;margin:1px 0 5px}
.hero-caption p{font-size:6.5px;line-height:1.5}
.hero-dots{position:absolute;left:50%;bottom:14px;transform:translateX(-50%);display:flex;gap:4px}
.hero-dots span{width:5px;height:5px;border-radius:50%;background:#ffffff80}
.hero-dots span:first-child{background:var(--white)}

.btn{display:inline-block;background:var(--orange);color:var(--white);font-size:5.5px;font-weight:700;padding:4px 9px;text-transform:uppercase;text-decoration:none}

.welcome{height:194px;flex:none;display:flex;gap:26px;padding:34px 42px 0}
.welcome-text{flex:1}
.welcome-text h2{font-size:15px;font-weight:600;margin-bottom:5px}
.welcome-text .lead{font-size:7px;font-weight:600;margin-bottom:5px;line-height:1.45}
.welcome-text p{font-size:5.8px;line-height:1.65;color:var(--muted)}
.calculator{width:150px;height:92px;background:var(--orange);color:var(--white);padding:10px;position:relative;margin-top:14px}
.calculator h3{font-size:10px;font-weight:700;line-height:1.15;width:80px}
.calculator p{font-size:5.3px;line-height:1.5;margin:6px 0 7px;width:100px}
.calculator .btn{background:var(--orange-dark)}
.calculator svg{position:absolute;right:10px;top:10px}

.features{height:218px;flex:none;display:flex;gap:20px;padding:0 42px}
.feature{flex:1}
.feature-photo{height:86px}
.feature h3{font-size:10px;font-weight:600;color:var(--orange);margin:8px 0 4px}
.feature p{font-size:5.5px;line-height:1.6;color:var(--muted);margin-bottom:7px}

.testimonials{height:205px;flex:none;background:var(--band);text-align:center;padding-top:62px}
.testimonials h2{font-size:16px;font-weight:600;margin-bottom:12px}
.quote{position:relative;width:480px;margin:0 auto;font-size:6.3px;line-height:1.75;color:var(--muted);font-style:italic}
.quote .mark{position:absolute;font-size:30px;color:var(--orange);font-style:normal;line-height:1}
.quote .open{left:-24px;top:-6px}.quote .close{right:-24px;bottom:-18px}
.author{font-size:6.5px;margin-top:10px;color:var(--ink)}

.site-footer{height:145px;flex:none;background:var(--footer);display:flex;padding:24px 42px 0;gap:28px}
.footer-col{flex:1}
.footer-col h4{font-size:7.5px;font-weight:700;color:var(--white);margin-bottom:5px}
.footer-col li{list-style:none;font-size:5.8px;color:var(--footer-text);line-height:1.75}
.footer-col p{font-size:5.8px;color:var(--footer-text);line-height:1.6}
.social{display:flex;gap:5px;margin-top:6px}
.social span{width:10px;height:10px;border-radius:50%;background:var(--footer-text)}
.legal{height:20px;flex:none;background:var(--bar);color:var(--footer-text);font-size:5px;line-height:20px;padding-left:42px}
</style>
</head>
<body>
<div class="page">
  <header class="site-header">
    <div class="brand"><span class="brand-square"></span>ROWEN</div>
    <div class="call">
      <small>CALL US NOW</small>
      <div class="phone">
        <svg width="11" height="11" viewBox="0 0 24 24"><path fill="#f08a1c" d="M6.6 10.8a15 15 0 0 0 6.6 6.6l2.2-2.2c.3-.3.7-.4 1-.2 1.1.4 2.3.6 3.6.6.6 0 1 .4 1 1V20c0 .6-.4 1-1 1A17 17 0 0 1 3 4c0-.6.4-1 1-1h3.5c.6 0 1 .4 1 1 0 1.3.2 2.5.6 3.6.1.3 0 .7-.2 1z"/></svg>
        (07) 5550 1234
      </div>
    </div>
  </header>
  <nav class="main-nav">
    <a class="active" href="#">HOME</a><a href="#">ABOUT US</a><a href="#">SERVICES</a><a href="#">PROJECTS</a><a href="#">OUR WORK</a><a href="#">CALCULATOR</a><a href="#">CONTACT US</a>
  </nav>
  <section class="hero" role="img" aria-label="Builder in hi-vis vest and hard hat working on a tiled roof under a blue sky">
    <div class="hero-caption">
      <div class="kicker">Installing Residential &amp; Commercial</div>
      <h1>Construction Services</h1>
      <p>Quality building, renovation and inspection work across the inner north-west suburbs of the city.</p>
      <p style="margin-top:7px"><a class="btn" href="#">Read More</a></p>
    </div>
    <div class="hero-dots"><span></span><span></span><span></span><span></span></div>
  </section>

  <section class="welcome">
    <div class="welcome-text">
      <h2>Welcome to the Rowen Group Pty Ltd</h2>
      <p class="lead">Do you need building advice, or simply someone to help you through the turbulence of the building industry?</p>
      <p>For over twenty years we have guided home owners through renovations, extensions and inspections with honest advice, clear pricing and careful workmanship. Our passion is building, and our promise is impeccable customer focus at every single step of the way.</p>
      <p style="margin-top:4px">We keep our process transparent, so you always know where your project stands from the first visit to the final handover of keys.</p>
    </div>
    <aside class="calculator">
      <h3>PROJECT CALCULATOR</h3>
      <svg width="22" height="28" viewBox="0 0 22 28"><rect x="1" y="1" width="20" height="26" rx="2" fill="none" stroke="#fff" stroke-width="2"/><rect x="4" y="4" width="14" height="6" fill="#fff"/><g fill="#fff"><rect x="4" y="13" width="3" height="3"/><rect x="9.5" y="13" width="3" height="3"/><rect x="15" y="13" width="3" height="3"/><rect x="4" y="18" width="3" height="3"/><rect x="9.5" y="18" width="3" height="3"/><rect x="15" y="18" width="3" height="3"/></g></svg>
      <p>Work out a rough budget for your project before you get in touch with our team.</p>
      <a class="btn" href="#">Read More</a>
    </aside>
  </section>

  <section class="features">
    <article class="feature">
      <div class="feature-photo" role="img" aria-label="Timber wall frame of a house under construction" style="background:linear-gradient(160deg,#e0c9a2 0%,#b8966a 55%,#8a6c4b 100%)"></div>
      <h3>How can we help you?</h3>
      <p>From first sketch to final coat, we manage extensions, alterations and renovations with care and attention.</p>
      <a class="btn" href="#">Read More</a>
    </article>
    <article class="feature">
      <div class="feature-photo" role="img" aria-label="Cracked brick wall showing a building defect" style="background:linear-gradient(160deg,#cdbba5 0%,#a48a70 55%,#6f5b49 100%)"></div>
      <h3>Do you need a building issue?</h3>
      <p>Pre-purchase and new home inspections that give you clear, honest answers before you commit.</p>
      <a class="btn" href="#">Read More</a>
    </article>
    <article class="feature">
      <div class="feature-photo" role="img" aria-label="Renovated brick home with tiled roof" style="background:linear-gradient(180deg,#cfdbe6 0%,#c9bfb2 40%,#9d8570 75%,#6e5a49 100%)"></div>
      <h3>Services Provides</h3>
      <p>Renovations, extensions, inspections and project management for homes across the north-west.</p>
      <a class="btn" href="#">Read More</a>
    </article>
  </section>

  <section class="testimonials">
    <h2>Client Testimonials</h2>
    <div class="quote">
      <span class="mark open">&ldquo;</span>
      The team made our extension simple from day one. Every cost was explained up front, the site was kept tidy and the build finished on time. We felt informed at every stage of the process and would not hesitate to recommend them to family and friends planning a renovation of their own home.
      <span class="mark close">&rdquo;</span>
    </div>
    <p class="author">- By Dan &amp; Mia Holloway</p>
  </section>

  <footer class="site-footer">
    <div class="footer-col"><h4>COMPANY</h4><ul><li>Why Choose Rowen Group</li><li>Newsletter</li><li>Contact Us</li><li>Latest News</li></ul></div>
    <div class="footer-col"><h4>SERVICES</h4><ul><li>Extensions</li><li>Renovations</li><li>Inspections</li><li>Project Management</li></ul></div>
    <div class="footer-col"><h4>SUPPORT</h4><ul><li>FAQ</li><li>Privacy Policy</li><li>Terms of Use</li><li>Contact</li></ul></div>
    <div class="footer-col"><h4>GET IN TOUCH</h4><p>Follow our latest projects</p><div class="social"><span></span><span></span><span></span></div></div>
  </footer>
  <div class="legal">&copy; 2014 Rowen Group Pty Ltd. All rights reserved.</div>
</div>
</body>
</html>
```